We need a business card for our gym. We are a PowerCore affiliate in Decatur Georgie established 2008. Our company name is Rally Functional Fitness. PowerCore Building Prime Fitness. Instagram and website is @rallygym. Hashtags we use #rallywithheart #madetorally We want something similar to the the black and neon green design attached but a different color scheme. No neon colors. Are company colors are the same as the blue and white card attached. We are open to ideas as far as colors however - just no neon.

Contact Information for Business Card

Rally Functional Fitness
472 Halvern Drive
Decatur GA 30041
Phone 404.555.0187 Website www.rallygym.example

Font styles to use
Other font styles liked:
• Futura Extra Bold Condensed

Colors

Designer to choose colors to be used in the design.

Requirements
Must have
• Our primary font we typically use for our name is Futura Extra Bold Condensed
Nice to have
• I attached a card from that is black and neon green from Zorva that we would like something similar. The blue and white is more similar to our colors. We also use have used black and white in the past. We use the chevrons as out logo. We are a PowerCore affiliate so I included a logo from them as well that may or may not be used on the card. Our instagram is @rallygym hashtags #madetorally #rallywithheart
Should not have
• No neon colors

```html
<!DOCTYPE html>
<html lang="en">
<head>
<meta charset="utf-8">
<title>Rally Functional Fitness – Business Card</title>
<link rel="stylesheet" href="https://fonts.googleapis.com/css2?family=Anton&family=Oswald:wght@600&family=Montserrat:wght@700&display=swap">
<style>
  :root {
    --stage: #c9cdd1;
    --brand-blue: #3f69a0;
    --brand-blue-light: #4673ab;
    --brand-blue-deep: #3a6094;
    --card-white: #f6f6f6;
    --card-white-shade: #e6e6e6;
    --ink-white: #f4f4f4;
  }
  * { box-sizing: border-box; margin: 0; padding: 0; }
  html, body {
    width: 1200px;
    height: 1200px;
    overflow: hidden;
    background: var(--stage);
  }
  .canvas {
    position: relative;
    width: 1200px;
    height: 1200px;
  }
  .card {
    position: absolute;
    left: 250px;
    width: 700px;
    height: 400px;
  }

  /* Front */
  .card-front { top: 147px; }
  .front-field {
    position: absolute;
    inset: 0;
    background: linear-gradient(100deg, var(--brand-blue-light) 0%, var(--brand-blue) 55%, var(--brand-blue-deep) 100%);
  }
  .front-title {
    position: absolute;
    left: 0;
    right: 0;
    text-align: center;
    color: var(--ink-white);
  }
  .wordmark {
    top: 88px;
    font-family: "Anton", "Impact", sans-serif;
    font-size: 122px;
    line-height: 1;
    letter-spacing: 1px;
  }
  .tagline {
    top: 208px;
    font-family: "Anton", "Impact", sans-serif;
    font-size: 44px;
    line-height: 1;
    letter-spacing: 0.5px;
  }
  .location {
    top: 282px;
    font-family: "Montserrat", "Arial", sans-serif;
    font-weight: 700;
    font-size: 21px;
    line-height: 1;
    letter-spacing: 9px;
    padding-left: 9px;
  }

  /* Back */
  .card-back {
    top: 652px;
    background: var(--brand-blue);
    padding: 10px 13px 10px 10px;
  }
  .back-panel {
    position: relative;
    width: 100%;
    height: 100%;
    background: linear-gradient(160deg, var(--card-white) 0%, #f1f1f1 60%, var(--card-white-shade) 100%);
    color: var(--brand-blue);
    font-family: "Oswald", "Arial Narrow", sans-serif;
    font-weight: 600;
  }
  .brand-name-mark {
    position: absolute;
    right: 30px;
    top: 28px;
    display: flex;
    align-items: center;
    gap: 14px;
    font-size: 58px;
    line-height: 1;
  }
  .brand-name-mark .mark-square {
    width: 34px;
    height: 34px;
    background: var(--brand-blue);
  }
  .business-name {
    position: absolute;
    left: 40px;
    top: 178px;
    font-size: 31px;
    line-height: 1;
  }
  .name-rule {
    position: absolute;
    left: 38px;
    top: 218px;
    width: 348px;
    height: 2px;
    background: var(--brand-blue);
  }
  .contact-list {
    position: absolute;
    left: 41px;
    top: 236px;
    list-style: none;
    font-size: 21px;
    line-height: 27.5px;
    letter-spacing: 0.4px;
  }
</style>
</head>
<body>
<main class="canvas">

  <section class="card card-front" aria-label="Business card front">
    <div class="front-field" role="img" aria-label="Blue background with repeating brand chevron pattern"></div>
    <h1 class="front-title wordmark">RALLY</h1>
    <p class="front-title tagline">FUNCTIONAL FITNESS</p>
    <p class="front-title location">DECATUR • GEORGIA</p>
  </section>

  <section class="card card-back" aria-label="Business card back">
    <div class="back-panel">
      <div class="brand-name-mark">
        <span class="mark-square" aria-hidden="true"></span>
        <span>RALLY</span>
      </div>
      <h2 class="business-name">Rally Functional Fitness</h2>
      <div class="name-rule" aria-hidden="true"></div>
      <ul class="contact-list">
        <li>472 Halvern Drive</li>
        <li>Decatur GA 30041</li>
        <li>Phone: 404.555.0187</li>
        <li>Website: www.rallygym.example</li>
      </ul>
    </div>
  </section>

</main>
</body>
</html>
```